Quillmere Supply Chain and Logistic Consulting

Please review the attached Business Card. I want as close to this card with the colors, fonts, and quality of the card as possible. The attached compass should replace the deer head on both sides of the card and the text should say:

Backside
Compass JPEG
Quillmere SC&L
A Supply Chain and Logistics Consulting Company

Frontside
Quillmere SC&L
Ray Falkner - Larkton Nevada
President
____________________________________
(555) 314-9027
QuillmereSCL@Examplemail.com
_____________________________________

Bottom Front Side

Target Market(s)

Businesses

Contact Information for Business Card

Backside
Compass JPEG
Quillmere SC&L

Frontside
Quillmere SC&L
President
(555) 314-9027
QuillmereSCL@Examplemail.com

Bottom Front Side

Font styles to use
Serif
Script

Colors

Designer to choose colors to be used in the design.

Requirements
Must have
• See attached card for reference
Nice to have
Should not have

```html
<!DOCTYPE html>
<html lang="en">
<head>
<meta charset="utf-8">
<title>Quillmere SC&amp;L Business Card</title>
<link rel="stylesheet" href="https://fonts.googleapis.com/css2?family=Cinzel:wght@500;600&family=Tinos:wght@400;700&display=swap">
<style>
  :root {
    --backdrop: #a0a0a0;
    --navy: #0c2a4b;
    --paper: #ffffff;
    --rule-light: #c9cfd6;
    --rule-dark: #4a6282;
  }
  * { box-sizing: border-box; margin: 0; padding: 0; }
  html, body { width: 1200px; height: 900px; overflow: hidden; }
  body { background: var(--backdrop); position: relative; }

  .card {
    position: absolute;
    top: 200px;
    width: 310px;
    height: 502px;
  }
  .card--front {
    left: 253px;
    background: var(--paper);
    color: var(--navy);
    border-radius: 56px 0 56px 0;
  }
  .card--back {
    left: 627px;
    background: var(--navy);
    color: var(--paper);
    border-radius: 0 56px 0 56px;
  }

  .brand-mark {
    position: absolute;
    left: 50%;
    width: 136px;
    height: 136px;
    margin-left: -68px;
    border-radius: 50%;
    border: 2px solid currentColor;
  }
  .card--front .brand-mark { top: 70px; }
  .card--back .brand-mark { top: 128px; }

  .brand-name {
    position: absolute;
    left: 0; right: 0;
    text-align: center;
    font-family: "Cinzel", serif;
    font-weight: 600;
    letter-spacing: 0.5px;
  }
  .card--front .brand-name { top: 232px; font-size: 23px; }
  .card--back .brand-name { top: 298px; font-size: 25px; }

  .contact {
    position: absolute;
    left: 29px;
    top: 314px;
    font-family: "Tinos", serif;
  }
  .contact__name { font-weight: 700; font-size: 17px; line-height: 22px; }
  .contact__title { font-size: 14px; line-height: 18px; }
  .contact__lines { margin-top: 9px; font-size: 14px; line-height: 18px; }
  .contact__line { display: flex; align-items: center; gap: 3px; }
  .contact__line svg { width: 13px; height: 11px; fill: var(--navy); }

  .divider {
    position: absolute;
    height: 1px;
  }
  .card--front .divider { left: 29px; right: 22px; top: 416px; background: var(--rule-light); }
  .card--back .divider { left: 28px; right: 26px; top: 408px; background: var(--rule-dark); }

  .tagline {
    position: absolute;
    font-family: "Cinzel", serif;
    font-weight: 600;
    font-size: 16px;
    line-height: 18px;
    letter-spacing: 0.3px;
  }
  .card--front .tagline { left: 29px; top: 423px; text-align: left; }
  .card--back .tagline { left: 0; right: 0; top: 415px; text-align: center; }
</style>
</head>
<body>
  <section class="card card--front" aria-label="Card front">
    <div class="brand-mark"></div>
    <h1 class="brand-name">QUILLMERE SC&amp;L</h1>
    <div class="contact">
      <p class="contact__name">Ray Falkner - Larkton Nevada</p>
      <p class="contact__title">President</p>
      <div class="contact__lines">
        <p class="contact__line">
          <svg viewBox="0 0 13 11" aria-hidden="true"><path d="M1 4 Q6.5 0 12 4 L10.5 5 L9 3.6 L4 3.6 L2.5 5 Z M3 5.5 L10 5.5 L12 10 L1 10 Z"/></svg>
          (555) 314-9027
        </p>
        <p class="contact__line">
          <svg viewBox="0 0 13 11" aria-hidden="true"><path d="M1 2 H12 V10 H1 Z M2 3 V3.4 L6.5 6.6 L11 3.4 V3 Z" fill-rule="evenodd"/></svg>
          QuillmereSCL@Examplemail.com
        </p>
      </div>
    </div>
    <div class="divider"></div>
    <p class="tagline">A Supply Chain and Logistics<br>Consulting Company</p>
  </section>

  <section class="card card--back" aria-label="Card back">
    <div class="brand-mark"></div>
    <h2 class="brand-name">QUILLMERE SC&amp;L</h2>
    <div class="divider"></div>
    <p class="tagline">A Supply Chain and Logistics<br>Consulting Company</p>
  </section>
</body>
</html>
```